Bright Harbor Brochure/Flyer Revisions

Improve the current design and over all look for Tri-Fold brochure and 8 x 11 flyer along with update the text and view picture substitutions.

Target Market(s)

Currently our brochure is geared more towards the Cancer Patient, and less Senior.
I want to take the new revisions text, or new message, and incorporate it into the new designed brochure and flyer. I want a nice picture of a senior or couple to be primary view shot and the cancer patients secondary.
Please visit our website; www.brightharbors-demo.org

Requirements
Must have
• we want all Seniors and Cancer Patients that own a life insurance policy, group or individual to call us. We want the consumer to be educated and know their rights.
Bright Harbors will be there ADVOCATE and Financial RESOURCE

```html
<!DOCTYPE html>
<html lang="en">
<head>
<meta charset="utf-8">
<title>Bright Harbors Tri-Fold Brochure</title>
<link rel="stylesheet" href="https://fonts.googleapis.com/css2?family=Didact+Gothic&family=Signika:wght@500;600;700&family=Arimo:wght@400;700&display=swap">
<style>
:root{
  --sky:#e9eff9;
  --blue:#2d6fc4;
  --navy:#2b3a8f;
  --purple:#8a2a8f;
  --mauve:#9b5b86;
  --gold:#f2b523;
  --ink:#2e2e2e;
  --tick:#c72f7c;
}
*{margin:0;padding:0;box-sizing:border-box}
html,body{width:1200px;height:934px;overflow:hidden;background:#f4f4f4}
.brochure{position:relative;width:1200px;height:934px;background:linear-gradient(180deg,#f7f9fd 0%,var(--sky) 60%,#dfe8f6 100%);font-family:"Didact Gothic",sans-serif;color:var(--ink);overflow:hidden}
.waves{position:absolute;inset:0}
.fold{position:absolute;top:0;bottom:0;width:1px;background:rgba(120,140,180,.35)}
.abs{position:absolute}
.brand{font-family:"Signika",sans-serif;font-weight:600;color:var(--blue);white-space:nowrap;display:flex;align-items:center;justify-content:center;gap:10px}
.brand .dot{width:14px;height:14px;border-radius:50%;background:var(--gold);flex:none}

/* left panel: contact frame */
.contact-box{left:28px;top:39px;width:347px;height:324px;border:2px solid var(--purple);border-radius:10px;text-align:center}
.contact-box > *{position:absolute;left:0;right:0}
.contact-box .brand{top:78px;font-size:28px;letter-spacing:3px}
.contact-box .return{top:158px;font-size:16px}
.contact-box .callfree{top:186px;font-family:"Arimo",sans-serif;font-weight:700;color:var(--navy);font-size:22px}
.contact-box .phone{top:214px;font-family:"Arimo",sans-serif;font-weight:700;color:var(--purple);font-size:42px;line-height:1.1}
.contact-box .confid{top:266px;font-size:17px}
.contact-box .confid-strong{top:292px;font-family:"Arimo",sans-serif;font-weight:700;color:var(--blue);font-size:21px}

/* left panel: reply mailer, turned a quarter clockwise */
.mailer{left:51px;top:368px;width:275px;height:293px;transform:rotate(90deg);transform-origin:center;font-family:"Arimo",sans-serif}
.mailer > *{position:absolute;left:0;right:0}
.mailer .slogan{top:0;font-family:"Signika",sans-serif;font-weight:700;color:var(--purple);font-size:28px;line-height:1.12;letter-spacing:1px;text-align:center}
.mailer .reply{top:96px;height:68px;background:linear-gradient(180deg,#f7e3ec,#e9b6cf);border-radius:8px;padding:8px 10px;display:flex;flex-direction:column-reverse;justify-content:center;gap:6px}
.mailer .reply b{display:block;font-size:18px;color:#222;letter-spacing:.5px;text-align:center;white-space:nowrap}
.mailer .reply span{display:flex;justify-content:space-between;font-size:9px;color:#444}
.mailer .postage-note{top:178px;font-size:11.5px;letter-spacing:.2px;text-align:center;white-space:nowrap}
.mailer .address{top:230px;font-size:17px;line-height:1.15;color:#111;padding-left:14px;white-space:nowrap}
.bars{left:90px;top:682px;display:flex;gap:14px}
.bars i{display:block;width:10px;height:131px;background:linear-gradient(180deg,var(--mauve),#f3d3e2)}
.stamp-box{left:212px;top:682px;width:128px;height:131px;border:2px solid var(--navy)}
.stamp-box p{position:absolute;left:50%;top:50%;width:124px;transform:translate(-50%,-50%) rotate(90deg);font-family:"Arimo",sans-serif;font-size:13px;line-height:1.12;text-align:center;color:#333}
.web{font-family:"Arimo",sans-serif;font-weight:700;color:var(--navy);font-size:19px;display:flex;align-items:center;gap:6px;white-space:nowrap}

/* middle panel */
.photo{background:radial-gradient(ellipse at 50% 55%,#e8d3c4 0%,#b8cbe6 45%,#6fa6e0 100%)}
.photo-oval{left:420px;top:63px;width:358px;height:241px;border-radius:50%}
.offer-title{left:451px;top:322px;font-family:"Signika",sans-serif;font-weight:700;color:var(--purple);font-size:38px;line-height:1.05;letter-spacing:.5px;white-space:nowrap}
.offer-title small{font-size:27px;color:var(--blue);font-weight:500;margin-right:12px}
.offer-title .you{display:block;text-align:right;font-size:26px;color:var(--blue);font-weight:500;margin-top:2px}
.benefits{left:440px;top:436px;list-style:none;font-size:15px;color:#333}
.benefits li{height:24.4px;display:flex;align-items:center;gap:6px;white-space:nowrap}
.benefits svg{width:18px;height:14px;flex:none}
.tagline{left:400px;width:400px;top:892px;text-align:center;font-family:"Arimo",sans-serif;font-weight:700;font-style:italic;color:var(--navy);font-size:22px}

/* right panel */
.cover-brand{left:800px;top:156px;width:400px}
.cover-brand .brand{font-size:32px;letter-spacing:3px}
.photo-couple{left:801px;top:262px;width:399px;height:534px;background:linear-gradient(180deg,#c9e1f3 0%,#e6d6c8 45%,#c8b2a0 75%,#d9e4f2 100%)}
.headline{left:875px;top:642px;font-family:"Signika",sans-serif;font-weight:700;line-height:1.13}
.headline .l1{color:var(--navy);font-size:36px;letter-spacing:9px}
.headline .l2,.headline .l3{color:var(--purple);font-size:42px;letter-spacing:4px}
.resources{left:818px;top:810px;width:370px;transform:rotate(-3.5deg);font-family:"Signika",sans-serif;font-weight:600;color:var(--gold);font-size:22px;text-align:center;letter-spacing:.5px;white-space:nowrap}
.help{left:800px;width:400px;top:854px;text-align:center;font-family:"Arimo",sans-serif;font-weight:700;font-size:20px;color:#222}
.cover-contact{left:819px;top:896px;display:flex;align-items:center;gap:12px;font-family:"Arimo",sans-serif;color:var(--navy);white-space:nowrap}
.cover-contact .tel{font-size:20px;font-weight:700;display:flex;align-items:center;gap:4px}
.cover-contact .site{font-size:13px;font-weight:700;display:flex;align-items:center;gap:3px}
</style>
</head>
<body>
<main class="brochure">
  <svg class="waves" width="1200" height="934" viewBox="0 0 1200 934" aria-hidden="true">
    <defs>
      <linearGradient id="band" x1="0" y1="0" x2="0" y2="1">
        <stop offset="0" stop-color="#6f9ddc"/><stop offset="1" stop-color="#c6d8f1"/>
      </linearGradient>
      <linearGradient id="footband" x1="0" y1="0" x2="0" y2="1">
        <stop offset="0" stop-color="#9cbbe7"/><stop offset="1" stop-color="#5f8fd4"/>
      </linearGradient>
    </defs>
    <path d="M0 0H400V130C300 40 150 60 0 70Z" fill="url(#band)" opacity=".55"/>
    <path d="M0 75C150 55 300 70 400 150" fill="none" stroke="#b56a96" stroke-width="5" opacity=".55"/>
    <path d="M400 0H800V60C650 30 500 60 400 150Z" fill="url(#band)" opacity=".55"/>
    <path d="M400 150C520 80 680 40 800 62" fill="none" stroke="#e9b9cf" stroke-width="5"/>
    <path d="M800 0H1200V80C1050 55 900 70 800 85Z" fill="url(#band)" opacity=".7"/>
    <path d="M800 95C950 80 1100 75 1200 90" fill="none" stroke="#b56a96" stroke-width="6" opacity=".7"/>
    <path d="M800 300C950 285 1100 278 1200 290V262H800Z" fill="#eef3fb"/>
    <path d="M800 318C950 290 1080 285 1200 295" fill="none" stroke="#a05887" stroke-width="8" opacity=".75"/>
    <path d="M0 825C150 850 300 865 400 875V934H0Z" fill="url(#footband)"/>
    <path d="M0 822C150 845 300 860 400 868" fill="none" stroke="#b56a96" stroke-width="6" opacity=".6"/>
    <path d="M400 875C550 865 700 855 800 845V934H400Z" fill="url(#footband)"/>
    <path d="M400 871C550 860 700 850 800 840" fill="none" stroke="#e9b9cf" stroke-width="4"/>
    <path d="M800 840C950 815 1100 805 1200 798V934H800Z" fill="url(#footband)"/>
    <path d="M800 880C950 860 1100 852 1200 850V934H800Z" fill="#dfe9f7"/>
    <path d="M800 892C950 872 1100 862 1200 860V934H800Z" fill="url(#footband)" opacity=".8"/>
  </svg>
  <span class="fold" style="left:400px"></span>
  <span class="fold" style="left:800px"></span>

  <!-- left panel: reply mailer -->
  <section class="abs contact-box">
    <div class="brand"><span class="dot"></span>BRIGHT HARBORS</div>
    <p class="return">Return the attached post card or</p>
    <p class="callfree">Call Toll Free</p>
    <p class="phone">800-555-0142</p>
    <p class="confid">All Communication will be</p>
    <p class="confid-strong">kept strickly confidential!</p>
  </section>

  <section class="abs mailer">
    <p class="slogan">RAISING<br>QUALITY OF LIFE</p>
    <div class="reply">
      <span><em>First-Class Mail</em><em>Permit No. 2040</em><em>ALDER, GA</em></span>
      <b>BUSINESS REPLY MAIL</b>
    </div>
    <p class="postage-note">POSTAGE WILL BE PAID BY ADDRESSEE</p>
    <p class="address">BRIGHT HARBORS<br>410 Meridian Way STE 200<br>ALDER GA 30000-1234</p>
  </section>

  <div class="abs bars" aria-hidden="true"><i></i><i></i><i></i><i></i><i></i></div>
  <div class="abs stamp-box"><p>NO POSTAGE<br>NECESSARY<br>IF MAILED<br>IN THE<br>UNITED STATES</p></div>

  <p class="abs web" style="left:52px;top:897px">
    <svg width="18" height="18" viewBox="0 0 18 18" aria-hidden="true"><circle cx="9" cy="9" r="7.5" fill="none" stroke="currentColor" stroke-width="1.6"/><path d="M1.5 9H16.5M9 1.5C5 6 5 12 9 16.5M9 1.5C13 6 13 12 9 16.5" fill="none" stroke="currentColor" stroke-width="1.3"/></svg>
    www.brightharbors-demo.org
  </p>

  <!-- middle panel: benefits -->
  <div class="abs photo photo-oval" role="img" aria-label="Photo of a young woman in a knit cap shading her eyes against a blue sky"></div>
  <h2 class="abs offer-title"><small>With</small>BRIGHT<br>HARBORS<span class="you">You can...</span></h2>
  <ul class="abs benefits">
    <li><svg viewBox="0 0 18 14"><path d="M1 7L6 12L17 1" fill="none" stroke="var(--tick)" stroke-width="3"/></svg>Reduce financial stress</li>
    <li><svg viewBox="0 0 18 14"><path d="M1 7L6 12L17 1" fill="none" stroke="var(--tick)" stroke-width="3"/></svg>Pay for uninsured Healthcare cost</li>
    <li><svg viewBox="0 0 18 14"><path d="M1 7L6 12L17 1" fill="none" stroke="var(--tick)" stroke-width="3"/></svg>Pay for alternative Treatment</li>
    <li><svg viewBox="0 0 18 14"><path d="M1 7L6 12L17 1" fill="none" stroke="var(--tick)" stroke-width="3"/></svg>Imptove Quality of Life</li>
    <li><svg viewBox="0 0 18 14"><path d="M1 7L6 12L17 1" fill="none" stroke="var(--tick)" stroke-width="3"/></svg>Pay Off Debt</li>
    <li><svg viewBox="0 0 18 14"><path d="M1 7L6 12L17 1" fill="none" stroke="var(--tick)" stroke-width="3"/></svg>Take a Vacation or Dream trip</li>
    <li><svg viewBox="0 0 18 14"><path d="M1 7L6 12L17 1" fill="none" stroke="var(--tick)" stroke-width="3"/></svg>Make cash gifts to family and friends</li>
    <li><svg viewBox="0 0 18 14"><path d="M1 7L6 12L17 1" fill="none" stroke="var(--tick)" stroke-width="3"/></svg>Fulfill life wishes</li>
    <li><svg viewBox="0 0 18 14"><path d="M1 7L6 12L17 1" fill="none" stroke="var(--tick)" stroke-width="3"/></svg>Pay for College funding</li>
    <li><svg viewBox="0 0 18 14"><path d="M1 7L6 12L17 1" fill="none" stroke="var(--tick)" stroke-width="3"/></svg>Make Home Improvements</li>
    <li><svg viewBox="0 0 18 14"><path d="M1 7L6 12L17 1" fill="none" stroke="var(--tick)" stroke-width="3"/></svg>Donate to Church or Charity</li>
    <li><svg viewBox="0 0 18 14"><path d="M1 7L6 12L17 1" fill="none" stroke="var(--tick)" stroke-width="3"/></svg>See the money enjoyed by relatives now</li>
    <li><svg viewBox="0 0 18 14"><path d="M1 7L6 12L17 1" fill="none" stroke="var(--tick)" stroke-width="3"/></svg>Invest in financial opportunities</li>
    <li><svg viewBox="0 0 18 14"><path d="M1 7L6 12L17 1" fill="none" stroke="var(--tick)" stroke-width="3"/></svg>Buy a New Car</li>
    <li><svg viewBox="0 0 18 14"><path d="M1 7L6 12L17 1" fill="none" stroke="var(--tick)" stroke-width="3"/></svg>Fund long turm care expenses</li>
    <li><svg viewBox="0 0 18 14"><path d="M1 7L6 12L17 1" fill="none" stroke="var(--tick)" stroke-width="3"/></svg>Plan ahead for Final Estate Needs</li>
  </ul>
  <p class="abs tagline">Hope is our desired gift to you!</p>

  <!-- right panel: cover -->
  <div class="abs cover-brand"><div class="brand"><span class="dot"></span>BRIGHT HARBORS</div></div>
  <div class="abs photo-couple" role="img" aria-label="Photo of a smiling senior couple embracing outdoors under a bright sky"></div>
  <h1 class="abs headline"><span class="l1">DISCOVER</span><br><span class="l2">FINANCIAL</span><br><span class="l3">FREEDOM</span></h1>
  <p class="abs resources">Financial Resources are Available</p>
  <p class="abs help">We are waiting to help?</p>
  <p class="abs cover-contact">
    <span class="tel"><svg width="20" height="20" viewBox="0 0 20 20" aria-hidden="true"><circle cx="10" cy="10" r="8.5" fill="none" stroke="currentColor" stroke-width="1.6"/><path d="M7 5.5L8.6 7.8L7.6 9C8.2 10.4 9.5 11.8 11 12.4L12.2 11.4L14.5 13L13.6 14.6C10 14.6 5.4 10 5.4 6.4Z" fill="currentColor"/></svg>800-555-0142</span>
    <span class="site"><svg width="12" height="12" viewBox="0 0 18 18" aria-hidden="true"><circle cx="9" cy="9" r="7.5" fill="none" stroke="currentColor" stroke-width="1.8"/><path d="M1.5 9H16.5M9 1.5C5 6 5 12 9 16.5M9 1.5C13 6 13 12 9 16.5" fill="none" stroke="currentColor" stroke-width="1.5"/></svg>www.brightharbors-demo.org</span>
  </p>
</main>
</body>
</html>
```